Business Card/ Email Signature Design Project

I am an Interior Designer. I need a business card that looks sophisticated stylish but simple in design. My work covers space design/ interior architecture/ furniture design/ product development & styling.

I have a very specific brief and know mostly what I want. I'm hoping to work with someone who can translate my ideas.

My branding should have a strong focus on my name, the majority of my work is referral based.
I'm keen to keep a monochromatic colour scheme: dark charcoal/ black/ white/ embossing/ silver. I'm not suggesting we use all that I've listed, they are possible ideas at this stage. I will need to be mindful of printing costs an also how I make the design work across, cards, letter heads, email logo and web design.

Theory behind images sent below;
1-Rug Image_(minus boarder) I was thinking this image could be used on the back of the card with my contact details over. I like that the lines are almost hand drawn and start to look free form. It's a subtle contrast to a more formal front of the card with my name.
2_Tomas Dreyer_I really like the orientation, the proportion of font on the card, the colour and the font. I like the lower case for my name and the upper case for 'Interior Design'. Not sure if it should be 'Interior Designer or Interior Design' at this stage, was leaning towards 'Interior Design'. Was thinking the 'i' and 'd' in my surname could be the colour eg 'silver'?? We can decide on this once we see it.

Look forward to hearing from you.
Cheers,
Noreen Balfour

Printing

Noreen Balfour Interior Design

```html
<!DOCTYPE html>
<html lang="en">
<head>
<meta charset="utf-8">
<title>Noreen Balfour Interior Design — Business Card</title>
<link rel="stylesheet" href="https://fonts.googleapis.com/css2?family=Roboto:wght@300;500&family=Roboto+Condensed:wght@700&display=swap">
<style>
  :root {
    --backdrop: #d9d5d0;
    --card-dark: #141414;
    --card-mid: #2b2b2b;
    --card-back-light: #383838;
    --card-back-dark: #232323;
    --silver: #c9c9c9;
    --silver-dim: #8a8a8a;
    --ink: #0d0d0d;
    --shadow: rgba(0, 0, 0, 0.45);
  }
  * { margin: 0; padding: 0; box-sizing: border-box; }
  html, body {
    width: 1200px;
    height: 750px;
    overflow: hidden;
    background: var(--backdrop);
  }
  .canvas {
    position: relative;
    width: 1200px;
    height: 750px;
  }
  .card {
    position: absolute;
    box-shadow: 0 6px 18px var(--shadow);
  }
  .card-back {
    left: 490px;
    top: 333px;
    width: 632px;
    height: 362px;
    background: radial-gradient(ellipse at 50% 30%, var(--card-back-light), var(--card-back-dark) 85%);
    z-index: 1;
  }
  .card-front {
    left: 95px;
    top: 58px;
    width: 655px;
    height: 379px;
    background: radial-gradient(ellipse at 50% 45%, var(--card-mid), var(--card-dark) 80%);
    z-index: 2;
    overflow: hidden;
  }
  .front-texture {
    position: absolute;
    inset: 0;
    background: radial-gradient(ellipse at 45% 40%, rgba(255,255,255,0.05), rgba(0,0,0,0) 70%);
  }
  .name {
    position: absolute;
    left: 98px;
    top: 128px;
    font-family: "Roboto", Arial, sans-serif;
    font-weight: 500;
    font-size: 62px;
    letter-spacing: -0.5px;
    line-height: 1;
    color: var(--silver);
    white-space: nowrap;
  }
  .discipline {
    position: absolute;
    left: 102px;
    top: 205px;
    font-family: "Roboto", Arial, sans-serif;
    font-weight: 300;
    font-size: 17px;
    letter-spacing: 17px;
    color: var(--silver-dim);
    white-space: nowrap;
  }
  .contact {
    position: absolute;
    left: 0;
    right: 0;
    top: 203px;
    text-align: center;
    font-family: "Roboto Condensed", "Arial Narrow", sans-serif;
    font-weight: 700;
    font-size: 23px;
    line-height: 27px;
    color: var(--ink);
    list-style: none;
    padding-left: 20px;
  }
</style>
</head>
<body>
  <main class="canvas">
    <section class="card card-front" aria-label="Card front">
      <div class="front-texture" role="img" aria-label="Subtle dark hand-drawn rug line pattern"></div>
      <h1 class="name">noreen balfour</h1>
      <p class="discipline">INTERIOR DESIGN</p>
    </section>
    <section class="card card-back" aria-label="Card back">
      <ul class="contact">
        <li>P.O BOX 204 KELSO VIC. 3190</li>
        <li>INTERIORS@NOREENBALFOUR.COM</li>
        <li>WWW.NOREENBALFOUR.COM</li>
        <li>0400-555-217</li>
      </ul>
    </section>
  </main>
</body>
</html>
```